Website Development for vaultmerrow.com.au

Build a new Wordpress/Responsive website for vaultmerrow.com.au

Target Market(s)

Compliance Managers, Risk Managers, Information Security and Cyber Security Professionals, Chief Data/Digital Officers, Chief Operating/Financial Officers, Business Continuity Professionals, Disaster Recovery Planners, Small Business Owners, Local/Federal Government entities

Industry/Entity Type

Data Service

Coding

Coded - Design and coding required

Number of Pages Required

5+ page

Font styles to use
Sans Serif

Colors

Designer to choose colors to be used in the design.

Requirements
Must have
• 1. Site Structure: Home Page plus the following chapter-pages for a) Services b) About c) Resources d) Blog e) Contact Us
• 2. Prefer site to built on wordpress and we can purchase a theme if needed (we currently use Kelp9 for other sites)
• 3. Blog needs to be wordpress based
• 4. We will host the site ourselves on our own servers
• 5. Responsive Design
Nice to have
• 1. Livechat capability/interface
• 2. Capability for marketing automation integration (such as hubspot, marketo, infusionsoft etc)
• 3. Capability for CRM integration (Salesforce)

```html
<!DOCTYPE html>
<html lang="en">
<head>
<meta charset="utf-8">
<title>Blog | Vaultmerrow</title>
<link href="https://fonts.googleapis.com/css2?family=Roboto:wght@400;500;700&family=Mulish:wght@400;600;700&display=swap" rel="stylesheet">
<style>
:root{
  --red:#e8202a;
  --red-dark:#a3121a;
  --ink:#222;
  --text:#555;
  --grey-bar:#8e8e8e;
  --grey-foot:#7a7a7a;
  --line:#e3e3e3;
  --soft:#f3f3f3;
  --white:#fff;
}
*{box-sizing:border-box;margin:0;padding:0}
html,body{width:1200px;height:2703px;overflow:hidden}
body{position:relative;background:var(--white);font-family:"Mulish",sans-serif;color:var(--text)}
a{color:inherit;text-decoration:none}
.abs{position:absolute}

/* top bar */
.topbar{left:0;top:0;width:1200px;height:48px;background:var(--grey-bar);color:var(--white);font-size:14px}
.topbar .contact{left:142px;top:0;height:48px;display:flex;align-items:center;gap:36px}
.topbar .contact span{display:flex;align-items:center;gap:10px}
.topbar .follow{right:142px;top:0;height:48px;display:flex;align-items:center;gap:6px;font-family:"Roboto",sans-serif;font-weight:700;font-size:14px}
.follow .sq{width:20px;height:20px;background:var(--red);border-radius:2px}
.follow .sq.b{background:#3aa9e6}.follow .sq.c{background:#2a6aa6}
.follow b{margin-right:6px}

/* nav */
.nav{left:0;top:48px;width:1200px;height:82px;background:#f7f7f7}
.brand{display:flex;align-items:center;gap:10px;font-family:"Roboto",sans-serif;font-weight:700;font-size:30px;color:var(--red)}
.brand .mark{width:30px;height:30px;background:var(--red)}
.nav .brand{left:142px;top:22px}
.menu{right:142px;top:0;height:82px;display:flex;gap:34px;align-items:center;font-family:"Roboto",sans-serif;font-size:15px;color:var(--ink)}
.menu .on{color:var(--red);position:relative}
.menu .on::before{content:"";position:absolute;left:0;right:0;top:-31px;height:4px;background:var(--red)}

/* hero */
.hero{left:0;top:130px;width:1200px;height:394px;background:var(--soft);overflow:hidden}
.hero .bg{left:0;top:0;width:1200px;height:350px;background:radial-gradient(circle at 30% 40%,#c8222a,#8a0f15 60%,#5e0a0e)}
.hero .globe{left:650px;top:0;width:500px;height:350px;background:radial-gradient(circle at 45% 50%,#f0404a,#b5161e 45%,rgba(120,10,15,0) 75%)}
.hero svg{left:0;top:0}
.hero h1{left:142px;top:54px;font-family:"Roboto",sans-serif;font-weight:400;font-size:40px;line-height:52px;color:var(--white);letter-spacing:.5px}
.hero h1 strong{font-weight:700}
.hero h1 small{display:block;font-size:28px;line-height:44px}
.crumb{left:142px;top:490px;font-family:"Roboto",sans-serif;font-size:14px;color:var(--ink);display:flex;gap:12px}
.crumb .here{color:var(--red);font-weight:700}

/* blog */
.page-title{left:0;width:1200px;top:590px;text-align:center;font-family:"Roboto",sans-serif;font-weight:500;font-size:40px;color:var(--ink)}
.card{width:290px}
.card .photo{position:relative;height:211px;background:linear-gradient(135deg,#8d8f94,#c8c9cc 55%,#e7e6e2)}
.card .date{position:absolute;left:6px;top:0;width:34px;height:42px;background:var(--red);color:var(--white);font-family:"Roboto",sans-serif;font-size:13px;line-height:15px;text-align:center;padding-top:5px}
.card .date b{display:block;font-size:17px;line-height:18px;font-weight:500}
.card h3{margin-top:18px;font-family:"Mulish",sans-serif;font-weight:600;font-size:13.5px;line-height:21px;color:var(--ink)}
.card p{margin-top:8px;font-size:12px;line-height:23px;color:var(--text)}
.card .more{display:flex;align-items:center;gap:6px;margin-top:14px;color:var(--red);font-size:14px}
.c1{left:142px}.c2{left:456px}
.r1{top:692px}.r2{top:1117px}.r3{top:1541px}

.pager{left:0;width:890px;top:1960px;display:flex;justify-content:center;gap:6px;font-size:12px}
.pager span{height:26px;line-height:24px;border:1px solid var(--line);padding:0 12px;color:var(--text)}
.pager .on{background:var(--red);color:var(--white);border-color:var(--red)}
.pager .next{background:#7f7f7f;color:var(--white);border-color:#7f7f7f;padding:0 22px}

/* sidebar */
.search{left:771px;top:692px;width:287px;height:37px;background:#f0f0f0;display:flex}
.search span{flex:1;padding-left:18px;line-height:37px;font-size:12px;color:#777}
.search i{width:42px;background:var(--red);display:flex;align-items:center;justify-content:center}
.widget{left:771px;width:287px;border:1px solid var(--line)}
.widget h4{height:37px;line-height:37px;padding-left:16px;background:var(--red);color:var(--white);font-family:"Roboto",sans-serif;font-weight:500;font-size:19px}
.widget ul{list-style:none;padding:6px 16px 6px}
.widget li{display:flex;justify-content:space-between;align-items:center;height:38px;border-bottom:1px solid #eee;font-size:12px;color:#444}
.widget li:last-child{border-bottom:0}
.widget li span::before{content:"»";margin-right:8px;color:#666}
.cats{top:758px;height:343px}
.posts{top:1132px;height:266px}
.tabs{display:flex;gap:8px;padding:12px 18px 0}
.tabs span{height:24px;line-height:24px;padding:0 18px;background:#7f7f7f;color:var(--white);font-size:11px}
.tabs .on{background:var(--red)}
.posts ul{padding-top:2px}

/* get started */
.cta{left:0;top:2058px;width:1200px;height:468px;background:linear-gradient(120deg,#ef3a42,#e2222b 55%,#d81d26)}
.cta h2{left:0;width:1200px;top:100px;text-align:center;font-family:"Roboto",sans-serif;font-weight:700;font-size:38px;color:var(--white)}
.form{left:313px;top:187px;width:642px;height:142px;border:1px solid rgba(255,255,255,.55);display:flex}
.form .fields{width:321px;border-right:1px solid rgba(255,255,255,.55)}
.form .fields div{height:47px;line-height:46px;padding-left:18px;border-bottom:1px solid rgba(255,255,255,.55);font-size:13px;color:rgba(255,255,255,.8)}
.form .fields div:first-child{color:var(--white)}
.form .fields div:last-child{border-bottom:0}
.form .msg{padding:12px 18px;font-size:13px;color:rgba(255,255,255,.8)}
.submit{left:535px;top:362px;width:130px;height:36px;background:#111;border-radius:18px;display:flex;align-items:center;gap:16px;padding-left:4px;color:var(--white);font-family:"Roboto",sans-serif;font-weight:500;font-size:14px}
.submit i{width:28px;height:28px;border-radius:50%;background:var(--red)}

/* footer */
.footer{left:0;top:2526px;width:1200px;height:177px;background:var(--grey-foot);color:var(--white)}
.footer .brand{left:142px;top:52px;color:var(--white)}
.footer .brand .mark{background:var(--white)}
.footer .menu{top:60px;height:44px;font-size:13px;color:var(--white);gap:40px}
.footer .rule{left:142px;top:134px;width:916px;height:1px;background:rgba(255,255,255,.25)}
.footer .copy{left:142px;top:148px;font-size:11px}
.footer .legal{right:142px;top:148px;font-size:11px}
.chat{left:1018px;top:2500px;width:44px;height:44px;border-radius:50%;background:var(--white);box-shadow:0 2px 8px rgba(0,0,0,.3);display:flex;align-items:center;justify-content:center}
.chat::after{content:"";position:absolute;right:2px;top:2px;width:10px;height:10px;border-radius:50%;background:var(--red)}
</style>
</head>
<body>

<header class="abs topbar">
  <div class="abs contact">
    <span><svg width="16" height="16" viewBox="0 0 24 24" fill="none" stroke="#fff" stroke-width="2"><path d="M5 3h4l2 5-3 2a11 11 0 0 0 6 6l2-3 5 2v4a2 2 0 0 1-2 2A17 17 0 0 1 3 5a2 2 0 0 1 2-2z"/></svg>+012-555-019</span>
    <span><svg width="18" height="14" viewBox="0 0 24 18" fill="none" stroke="#fff" stroke-width="2"><rect x="1" y="1" width="22" height="16"/><path d="M1 1l11 9 11-9"/></svg>info@vaultmerrow.com.au</span>
  </div>
  <div class="abs follow"><b>Follow Us on</b><i class="sq"></i><i class="sq b"></i><i class="sq c"></i><i class="sq"></i></div>
</header>

<nav class="abs nav">
  <a class="abs brand" href="#"><i class="mark"></i>Vaultmerrow</a>
  <div class="abs menu"><a>HOME</a><a>ABOUT</a><a>SERVICES</a><a>RESOURCES</a><a class="on">BLOG</a><a>CONTACT US</a></div>
</nav>

<section class="abs hero">
  <div class="abs bg" role="img" aria-label="Red bokeh background photo"></div>
  <div class="abs globe" role="img" aria-label="Hands holding a glowing red sphere of digital service icons"></div>
  <svg class="abs" width="1200" height="394" viewBox="0 0 1200 394"><path d="M0 250 Q450 470 1200 280 L1200 394 L0 394Z" fill="#f3f3f3"/></svg>
  <h1 class="abs">DELIVERING <strong>QUALITY</strong><br>SERVICES THROUGH<br><strong>INNOVATION</strong><small>From Industry Experts</small></h1>
</section>
<div class="abs crumb"><span>HOME</span><span>»</span><span class="here">BLOG</span></div>

<h2 class="abs page-title">BLOG</h2>

<article class="abs card c1 r1"><div class="photo" role="img" aria-label="Business team reviewing documents"><span class="date">FEB<b>07</b></span></div><h3>Lorem ipsum dolor sit amet, consectetuer adipiscing elit, sed diam nonummy</h3><p>olore magna aliquam erat volutpat. Ut wisi enim minim veniam, quis nostrud exerci tationcorper suscipit lobortis nisl ut aliquip ex ea</p><a class="more">Read More <svg width="22" height="10" viewBox="0 0 22 10" fill="none" stroke="#e8202a" stroke-width="1.6"><path d="M0 5h20M16 1l4 4-4 4"/></svg></a></article>
<article class="abs card c2 r1"><div class="photo" role="img" aria-label="Overhead view of a planning meeting"><span class="date">FEB<b>07</b></span></div><h3>Lorem ipsum dolor sit amet, consectetuer adipiscing elit, sed diam nonummy</h3><p>olore magna aliquam erat volutpat. Ut wisi enim minim veniam, quis nostrud exerci tationcorper suscipit lobortis nisl ut aliquip ex ea</p><a class="more">Read More <svg width="22" height="10" viewBox="0 0 22 10" fill="none" stroke="#e8202a" stroke-width="1.6"><path d="M0 5h20M16 1l4 4-4 4"/></svg></a></article>
<article class="abs card c1 r2"><div class="photo" role="img" aria-label="Office staff working at desks"><span class="date">FEB<b>07</b></span></div><h3>Lorem ipsum dolor sit amet, consectetuer adipiscing elit, sed diam nonummy</h3><p>olore magna aliquam erat volutpat. Ut wisi enim minim veniam, quis nostrud exerci tationcorper suscipit lobortis nisl ut aliquip ex ea</p><a class="more">Read More <svg width="22" height="10" viewBox="0 0 22 10" fill="none" stroke="#e8202a" stroke-width="1.6"><path d="M0 5h20M16 1l4 4-4 4"/></svg></a></article>
<article class="abs card c2 r2"><div class="photo" style="background:linear-gradient(135deg,#1e2024,#4a4d52 60%,#7d7a74)" role="img" aria-label="Dark workstation with multiple monitors"><span class="date">FEB<b>07</b></span></div><h3>Lorem ipsum dolor sit amet, consectetuer adipiscing elit, sed diam nonummy</h3><p>olore magna aliquam erat volutpat. Ut wisi enim minim veniam, quis nostrud exerci tationcorper suscipit lobortis nisl ut aliquip ex ea</p><a class="more">Read More <svg width="22" height="10" viewBox="0 0 22 10" fill="none" stroke="#e8202a" stroke-width="1.6"><path d="M0 5h20M16 1l4 4-4 4"/></svg></a></article>
<article class="abs card c1 r3"><div class="photo" style="background:linear-gradient(135deg,#3a5f7a,#9fb4c2 55%,#e0e3e6)" role="img" aria-label="Network cabling in a server panel"><span class="date">FEB<b>07</b></span></div><h3>Lorem ipsum dolor sit amet, consectetuer adipiscing elit, sed diam nonummy</h3><p>olore magna aliquam erat volutpat. Ut wisi enim minim veniam, quis nostrud exerci tationcorper suscipit lobortis nisl ut aliquip ex ea</p><a class="more">Read More <svg width="22" height="10" viewBox="0 0 22 10" fill="none" stroke="#e8202a" stroke-width="1.6"><path d="M0 5h20M16 1l4 4-4 4"/></svg></a></article>
<article class="abs card c2 r3"><div class="photo" style="background:linear-gradient(135deg,#6b5a48,#a89680 55%,#d8d2c8)" role="img" aria-label="Laptops on a shared meeting table"><span class="date">FEB<b>07</b></span></div><h3>Lorem ipsum dolor sit amet, consectetuer adipiscing elit, sed diam nonummy</h3><p>olore magna aliquam erat volutpat. Ut wisi enim minim veniam, quis nostrud exerci tationcorper suscipit lobortis nisl ut aliquip ex ea</p><a class="more">Read More <svg width="22" height="10" viewBox="0 0 22 10" fill="none" stroke="#e8202a" stroke-width="1.6"><path d="M0 5h20M16 1l4 4-4 4"/></svg></a></article>

<div class="abs pager"><span>Previous</span><span class="on">1</span><span>2</span><span>3</span><span class="next">Next</span></div>

<aside>
  <div class="abs search"><span>Search Blog</span><i><svg width="16" height="16" viewBox="0 0 24 24" fill="none" stroke="#fff" stroke-width="3"><circle cx="10" cy="10" r="7"/><path d="M15 15l6 6"/></svg></i></div>
  <div class="abs widget cats"><h4>Categories</h4><ul>
    <li><span>Lorem Ipsum is simply dummy</span>(02)</li>
    <li><span>Lorem Ipsum is simply dummy</span>(08)</li>
    <li><span>Lorem Ipsum is simply dummy</span>(05)</li>
    <li><span>Lorem Ipsum is simply dummy</span>(11)</li>
    <li><span>Lorem Ipsum is simply dummy</span>(06)</li>
    <li><span>Lorem Ipsum is simply dummy</span>(18)</li>
    <li><span>Lorem Ipsum is simply dummy</span>(13)</li>
    <li><span>Lorem Ipsum is simply dummy</span>(20)</li>
  </ul></div>
  <div class="abs widget posts"><h4>Posts</h4>
    <div class="tabs"><span class="on">Popular</span><span>Commented</span><span>Tags</span></div>
    <ul>
      <li><span>Lorem Ipsum is simply dummy...</span></li>
      <li><span>Lorem Ipsum is simply dummy...</span></li>
      <li><span>Lorem Ipsum is simply dummy...</span></li>
      <li><span>Lorem Ipsum is simply dummy...</span></li>
      <li><span>Lorem Ipsum is simply dummy...</span></li>
    </ul></div>
</aside>

<section class="abs cta" role="img" aria-label="Red-tinted photo of a team working together">
  <h2 class="abs">LET’S GET STARTED</h2>
  <div class="abs form">
    <div class="fields"><div>Your Name*</div><div>Your Email*</div><div>Your Contact Number*</div></div>
    <div class="msg">Your Message*</div>
  </div>
  <div class="abs submit"><i></i>Submit</div>
</section>

<footer class="abs footer">
  <div class="abs brand"><i class="mark"></i>Vaultmerrow</div>
  <div class="abs menu"><a>HOME</a><a>ABOUT</a><a>SERVICES</a><a>RESOURCES</a><a>BLOG</a><a>CONTACT US</a></div>
  <div class="abs rule"></div>
  <div class="abs copy">Copyright 2019 @ Vaultmerrow. All Rights Reserved.</div>
  <div class="abs legal">Terms of Services / Privacy Policy</div>
</footer>

<div class="abs chat"><svg width="22" height="20" viewBox="0 0 24 22" fill="#444"><path d="M2 3h20v13H9l-5 4v-4H2z"/><circle cx="8" cy="9.5" r="1.4" fill="#fff"/><circle cx="12" cy="9.5" r="1.4" fill="#fff"/><circle cx="16" cy="9.5" r="1.4" fill="#fff"/></svg></div>

</body>
</html>
```